Brightmill Data Works

Our company is about IT hardwares and IT solutions. IT hardware such as PC, RAMS, storage and servers. IT solutions such as project management, BA. We are also selling new technology too.

Target Market(s)

Consumer, Small to Medium Business, Corporate

Requirements
Must have
• The business card must have the following:
• Name:
• Title:
• Contact Number:
• Email address:
• Website:
• Color: Must match the logo color upgrade

```html
<!DOCTYPE html>
<html lang="en">
<head>
<meta charset="utf-8">
<title>Brightmill Data Works – Business Card</title>
<link rel="stylesheet" href="https://fonts.googleapis.com/css2?family=Archivo:wght@400;700;800&display=swap">
<style>
  :root {
    --backdrop: #2b2b2b;
    --card-white: #ffffff;
    --card-shade: #ececec;
    --charcoal: #3a3a3a;
    --ink: #333333;
    --muted: #6e6e6e;
    --amber: #c9862a;
  }
  * { box-sizing: border-box; margin: 0; padding: 0; }
  html, body { width: 1200px; height: 997px; overflow: hidden; }
  body {
    background: var(--backdrop);
    font-family: "Archivo", Arial, sans-serif;
    position: relative;
  }
  .card {
    position: absolute;
    width: 600px;
    height: 343px;
    background: linear-gradient(160deg, var(--card-white) 40%, var(--card-shade));
    box-shadow: 0 14px 30px rgba(0,0,0,.55);
    overflow: hidden;
  }
  .card-back { left: 70px; top: 90px; }
  .card-front { left: 530px; top: 500px; }

  .base-band {
    position: absolute; left: 0; right: 0; bottom: 0;
    background: var(--charcoal);
    border-top: 3px solid var(--amber);
  }
  .card-back .base-band { height: 12px; }
  .card-front .base-band { height: 34px; }

  .back-name {
    position: absolute; left: 0; right: 0; top: 138px;
    text-align: center;
    font-weight: 800; font-size: 34px; letter-spacing: 1px;
    text-transform: uppercase; color: var(--ink);
  }

  .brand-square {
    position: absolute; left: 40px; top: 58px;
    width: 118px; height: 118px;
    background: var(--charcoal);
  }
  .front-name {
    position: absolute; left: 190px; right: 30px; top: 78px;
    font-weight: 800; font-size: 30px; letter-spacing: .5px;
    text-transform: uppercase; color: var(--ink);
    text-align: right;
  }
  .holder {
    position: absolute; left: 40px; top: 196px;
  }
  .holder-name {
    font-weight: 700; font-size: 17px; color: var(--amber);
    text-transform: uppercase; letter-spacing: .5px;
  }
  .holder-title {
    font-weight: 700; font-size: 12px; color: var(--ink); margin-bottom: 8px;
  }
  .contact-list { list-style: none; }
  .contact-list li {
    display: flex; align-items: center; gap: 9px;
    font-size: 15px; color: var(--muted); line-height: 22px;
  }
  .contact-icon {
    width: 15px; height: 15px; border-radius: 50%;
    background: var(--charcoal);
    display: inline-flex; align-items: center; justify-content: center;
  }
  .website {
    position: absolute; right: 32px; bottom: 62px;
    font-weight: 700; font-size: 14px; letter-spacing: 1px; color: var(--ink);
  }
</style>
</head>
<body>

<section class="card card-back">
  <p class="back-name">Brightmill Data Works</p>
  <div class="base-band"></div>
</section>

<section class="card card-front">
  <div class="brand-square"></div>
  <p class="front-name">Brightmill Data Works</p>

  <div class="holder">
    <p class="holder-name">Dana Whitfield</p>
    <p class="holder-title">Director</p>
    <ul class="contact-list">
      <li>
        <span class="contact-icon">
          <svg width="9" height="9" viewBox="0 0 10 10"><path d="M2 1 L4 1 L4.6 3 L3.4 4 Q4.5 6 6 6.6 L7 5.4 L9 6 L9 8 Q5 9 1 3 Z" fill="#fff"/></svg>
        </span>555.014.2286
      </li>
      <li>
        <span class="contact-icon">
          <svg width="9" height="9" viewBox="0 0 10 10"><rect x="1.5" y="3" width="7" height="5" rx="1" fill="#fff"/><rect x="3" y="1.5" width="4" height="2" fill="#fff"/></svg>
        </span>555.019.7304
      </li>
      <li>
        <span class="contact-icon">
          <svg width="9" height="9" viewBox="0 0 10 10"><rect x="1" y="2.5" width="8" height="5.5" fill="#fff"/><path d="M1 2.5 L5 6 L9 2.5" stroke="#3a3a3a" stroke-width="1" fill="none"/></svg>
        </span>dana@brightmill.com
      </li>
    </ul>
  </div>

  <p class="website">www.brightmill.com</p>
  <div class="base-band"></div>
</section>

</body>
</html>
```